Aerospace Center needs app design

We need a design that would be a creative and innovative look of a simple idea connecting air traffic control situations with sonification.
We would like to see designs that use the elements shown in the short video which are different pads, showing 4 different colors, connecting with a degree and feeling of urgency. The different pads will be movable over screen, similar as to a whiteboard where you can move things around. Each of those pads has 4 different elements that are shown:
- ATC Event (you can chose different setups)
- Select a status (you can chose between Information, Caution and Alert. Color needs to feel more alert from Information to Alert.
- Notes box (you can open the box and write additional text on it)
- Music (you can chose different files. on the right side you can see a small group of notes. When you hover over the notes, music will be played without pressing a play or stop button.
The second video is an overview of music archival program that is connected with the pads.
Look and feel
Each slider illustrates characteristics of the customer's brand and the style your logo design should communicate.

```html
<!DOCTYPE html>
<html lang="en">
<head>
<meta charset="utf-8">
<title>ATC Sonification Pads</title>
<link href="https://fonts.googleapis.com/css2?family=Arimo:wght@400;700&display=swap" rel="stylesheet">
<style>
  :root{
    --page:#ffffff;
    --label:#9966f5;
    --info-frame:#3cfdb9;
    --info-row-top:#36eaaa;
    --info-row-bottom:#2fd79d;
    --info-hover:#6affc8;
    --info-ink:#ffffff;
    --caution-frame:#fafa00;
    --caution-row-top:#ecec38;
    --caution-row-bottom:#d3d46c;
    --caution-active-top:#ffe41a;
    --caution-active-bottom:#ffbe24;
    --caution-ink:#5a5a5a;
    --alert-frame:#ff0068;
    --alert-row-top:#e42c78;
    --alert-row-bottom:#c25a88;
    --alert-active-top:#ff3a4c;
    --alert-active-bottom:#ff7a2e;
    --alert-ink:#000000;
    --menu-ink:#666666;
    --menu-faint:#dddddd;
    --ring:#ffffff;
  }
  *{box-sizing:border-box;margin:0;padding:0}
  html,body{width:1200px;height:1200px;overflow:hidden;background:var(--page)}
  body{position:relative;font-family:'Arimo',Arial,sans-serif}

  .state-label{position:absolute;color:var(--label);font-size:37px;line-height:44px;text-align:center;font-weight:400}

  .pad{position:absolute;width:274px;height:368px;border-radius:40px;background:var(--frame)}
  .pad::before{content:"";position:absolute;left:9px;top:9px;width:256px;height:350px;border:4px solid var(--ring);border-radius:32px}
  .pad--info{--frame:var(--info-frame);--row-top:var(--info-row-top);--row-bottom:var(--info-row-bottom);--ink:var(--info-ink)}
  .pad--caution{--frame:var(--caution-frame);--row-top:var(--caution-row-top);--row-bottom:var(--caution-row-bottom);--ink:var(--caution-ink)}
  .pad--alert{--frame:var(--alert-frame);--row-top:var(--alert-row-top);--row-bottom:var(--alert-row-bottom);--ink:var(--alert-ink)}

  .pad__title{position:absolute;left:39px;top:17px;font-size:30px;font-weight:700;color:var(--ink)}
  .pad__close{position:absolute;left:218px;top:21px;width:22px;height:22px}
  .pad__close line{stroke:var(--ink);stroke-width:5;stroke-linecap:square}

  .field{position:absolute;left:23px;height:64px;border-radius:12px;background:linear-gradient(var(--row-top),var(--row-bottom));color:var(--ink);font-size:25px;font-weight:700;line-height:64px;padding-left:10px;white-space:nowrap}
  .field--wide{width:226px}
  .field--narrow{width:166px}
  .toggle{position:absolute;left:192px;width:57px;height:64px;border-radius:12px;background:linear-gradient(var(--row-top),var(--row-bottom))}
  .toggle svg{position:absolute;left:0;top:0;width:57px;height:64px}
  .toggle .chev{fill:none;stroke:var(--frame);stroke-width:9;opacity:.55}
  .toggle .staff line{stroke:var(--ink);stroke-width:1.3}
  .toggle .staff .note{fill:var(--ink)}
  .row-1{top:59px}.row-2{top:127px}.row-3{top:196px}.row-4{top:265px}
  .is-hover{background:var(--info-hover)}
  .is-caution{background:linear-gradient(var(--caution-active-top),var(--caution-active-bottom))}
  .is-alert{background:linear-gradient(var(--alert-active-top),var(--alert-active-bottom))}

  .menu{position:absolute;background:#fff;border-radius:14px;box-shadow:0 6px 0 rgba(47,215,157,.55)}
  .menu__item{font-size:25px;font-weight:700;color:var(--menu-ink);line-height:27px}
  .menu__item--current{color:var(--menu-faint)}
  .library{position:absolute;background:#fff;border-radius:14px;box-shadow:0 7px 0 #7de0bd;display:flex;align-items:center;justify-content:center;font-size:25px;font-weight:700;color:var(--menu-ink)}

  .cursor{position:absolute;width:42px;height:42px}
  .waves{position:absolute}
  .waves path{fill:none;stroke:var(--label);stroke-width:6}
</style>
</head>
<body>

<div class="state-label" style="left:487px;top:153px;width:200px">on mouse<br>over</div>
<div class="state-label" style="left:852px;top:175px;width:200px">on click</div>

<!-- Information pad, resting -->
<div class="pad pad--info" style="left:119px;top:245px">
  <div class="pad__title">AB1</div>
  <svg class="pad__close" viewBox="0 0 22 22"><line x1="3" y1="3" x2="19" y2="19"/><line x1="19" y1="3" x2="3" y2="19"/></svg>
  <div class="field field--narrow row-1">Event</div>
  <div class="toggle row-1"><svg viewBox="0 0 57 64"><polyline class="chev" points="0,22 28,38 57,22"/></svg></div>
  <div class="field field--narrow row-2">Status</div>
  <div class="toggle row-2"><svg viewBox="0 0 57 64"><polyline class="chev" points="0,22 28,38 57,22"/></svg></div>
  <div class="field field--wide row-3">Notes</div>
  <div class="field field--narrow row-4"></div>
  <div class="toggle row-4"><svg viewBox="0 0 57 64"><g class="staff"><line x1="5" y1="19" x2="52" y2="19"/><line x1="5" y1="25" x2="52" y2="25"/><line x1="5" y1="31" x2="52" y2="31"/><line x1="5" y1="37" x2="52" y2="37"/><line x1="5" y1="43" x2="52" y2="43"/><ellipse class="note" cx="24" cy="39" rx="7" ry="5"/><line x1="30" y1="39" x2="30" y2="13" style="stroke-width:2"/><path class="note" d="M30 13 L38 22 L30 20Z"/></g></svg></div>
</div>

<!-- Information pad, hover -->
<div class="pad pad--info" style="left:461px;top:245px">
  <div class="pad__title">AB1</div>
  <svg class="pad__close" viewBox="0 0 22 22"><line x1="3" y1="3" x2="19" y2="19"/><line x1="19" y1="3" x2="3" y2="19"/></svg>
  <div class="field field--narrow row-1 is-hover">Event</div>
  <div class="toggle row-1 is-hover"><svg viewBox="0 0 57 64"><polyline class="chev" points="0,22 28,38 57,22"/></svg></div>
  <div class="field field--narrow row-2">Information</div>
  <div class="toggle row-2"><svg viewBox="0 0 57 64"><polyline class="chev" points="0,22 28,38 57,22"/></svg></div>
  <div class="field field--wide row-3">Notes</div>
  <div class="field field--narrow row-4 is-hover">Halvor..........</div>
  <div class="toggle row-4 is-hover"><svg viewBox="0 0 57 64"><g class="staff"><line x1="5" y1="19" x2="52" y2="19"/><line x1="5" y1="25" x2="52" y2="25"/><line x1="5" y1="31" x2="52" y2="31"/><line x1="5" y1="37" x2="52" y2="37"/><line x1="5" y1="43" x2="52" y2="43"/><ellipse class="note" cx="24" cy="39" rx="7" ry="5"/><line x1="30" y1="39" x2="30" y2="13" style="stroke-width:2"/><path class="note" d="M30 13 L38 22 L30 20Z"/></g></svg></div>
</div>
<svg class="waves" style="left:700px;top:470px" width="80" height="84" viewBox="0 0 80 84">
  <path d="M6 8 A70 70 0 0 1 70 80"/>
  <path d="M10 30 A48 48 0 0 1 50 78"/>
  <path d="M12 50 A26 26 0 0 1 30 76"/>
</svg>

<!-- Information pad, click -->
<div class="pad pad--info" style="left:828px;top:244px">
  <div class="pad__title">AB1</div>
  <svg class="pad__close" viewBox="0 0 22 22"><line x1="3" y1="3" x2="19" y2="19"/><line x1="19" y1="3" x2="3" y2="19"/></svg>
  <div class="field field--narrow row-1 is-hover">Event</div>
  <div class="toggle row-1 is-hover"><svg viewBox="0 0 57 64"><polyline class="chev" points="0,22 28,38 57,22"/></svg></div>
  <div class="field field--wide row-3"></div>
  <div class="field field--narrow row-4 is-hover">Halvor..........</div>
  <div class="toggle row-4 is-hover"><svg viewBox="0 0 57 64"><g class="staff"><line x1="5" y1="19" x2="52" y2="19"/><line x1="5" y1="25" x2="52" y2="25"/><line x1="5" y1="31" x2="52" y2="31"/><line x1="5" y1="37" x2="52" y2="37"/><line x1="5" y1="43" x2="52" y2="43"/><ellipse class="note" cx="24" cy="39" rx="7" ry="5"/><line x1="30" y1="39" x2="30" y2="13" style="stroke-width:2"/><path class="note" d="M30 13 L38 22 L30 20Z"/></g></svg></div>
  <div class="menu" style="left:17px;top:127px;width:238px;height:124px;padding:4px 0 0 16px">
    <div class="menu__item menu__item--current">Event</div>
    <div class="menu__item">Landing</div>
    <div class="menu__item">Departure</div>
  </div>
  <div class="library" style="left:16px;top:332px;width:240px;height:126px">Music library</div>
</div>

<!-- Caution pad -->
<div class="pad pad--caution" style="left:119px;top:732px">
  <div class="pad__title">AB1</div>
  <svg class="pad__close" viewBox="0 0 22 22"><line x1="3" y1="3" x2="19" y2="19"/><line x1="19" y1="3" x2="3" y2="19"/></svg>
  <div class="field field--narrow row-1">Event</div>
  <div class="toggle row-1"><svg viewBox="0 0 57 64"><polyline class="chev" points="0,22 28,38 57,22"/></svg></div>
  <div class="field field--narrow row-2 is-caution">Caution</div>
  <div class="toggle row-2 is-caution"><svg viewBox="0 0 57 64"><polyline class="chev" points="0,22 28,38 57,22"/></svg></div>
  <div class="field field--wide row-3">Notes</div>
  <div class="field field--narrow row-4"></div>
  <div class="toggle row-4"><svg viewBox="0 0 57 64"><g class="staff"><line x1="5" y1="19" x2="52" y2="19"/><line x1="5" y1="25" x2="52" y2="25"/><line x1="5" y1="31" x2="52" y2="31"/><line x1="5" y1="37" x2="52" y2="37"/><line x1="5" y1="43" x2="52" y2="43"/><ellipse class="note" cx="24" cy="39" rx="7" ry="5"/><line x1="30" y1="39" x2="30" y2="13" style="stroke-width:2"/><path class="note" d="M30 13 L38 22 L30 20Z"/></g></svg></div>
</div>

<!-- Alert pad -->
<div class="pad pad--alert" style="left:451px;top:732px">
  <div class="pad__title">AB1</div>
  <svg class="pad__close" viewBox="0 0 22 22" style="--ink:#fff"><line x1="3" y1="3" x2="19" y2="19"/><line x1="19" y1="3" x2="3" y2="19"/></svg>
  <div class="field field--narrow row-1 is-alert">Event</div>
  <div class="toggle row-1 is-alert"><svg viewBox="0 0 57 64"><polyline class="chev" points="0,22 28,38 57,22"/></svg></div>
  <div class="field field--narrow row-2">Alert</div>
  <div class="toggle row-2"><svg viewBox="0 0 57 64"><polyline class="chev" points="0,22 28,38 57,22"/></svg></div>
  <div class="field field--wide row-3">Notes</div>
  <div class="field field--narrow row-4"></div>
  <div class="toggle row-4"><svg viewBox="0 0 57 64"><g class="staff"><line x1="5" y1="19" x2="52" y2="19"/><line x1="5" y1="25" x2="52" y2="25"/><line x1="5" y1="31" x2="52" y2="31"/><line x1="5" y1="37" x2="52" y2="37"/><line x1="5" y1="43" x2="52" y2="43"/><ellipse class="note" cx="24" cy="39" rx="7" ry="5"/><line x1="30" y1="39" x2="30" y2="13" style="stroke-width:2"/><path class="note" d="M30 13 L38 22 L30 20Z"/></g></svg></div>
</div>

<!-- Pointer marks -->
<svg class="cursor" style="left:597px;top:327px" viewBox="0 0 42 42"><path d="M0 0 L40 12 L28 19 L42 33 L35 40 L21 26 L13 38 Z" fill="#000"/></svg>
<svg class="cursor" style="left:671px;top:552px" viewBox="0 0 42 42"><path d="M0 0 L40 12 L28 19 L42 33 L35 40 L21 26 L13 38 Z" fill="#000"/></svg>
<svg class="cursor" style="left:1051px;top:329px" viewBox="0 0 42 42"><path d="M0 0 L40 12 L28 19 L42 33 L35 40 L21 26 L13 38 Z" fill="#000"/></svg>
<svg class="cursor" style="left:963px;top:546px" viewBox="0 0 42 42"><path d="M0 0 L40 12 L28 19 L42 33 L35 40 L21 26 L13 38 Z" fill="#000"/></svg>
<svg class="cursor" style="left:266px;top:890px" viewBox="0 0 42 42"><path d="M0 0 L40 12 L28 19 L42 33 L35 40 L21 26 L13 38 Z" fill="#000"/></svg>
<svg class="cursor" style="left:607px;top:825px" viewBox="0 0 42 42"><path d="M0 0 L40 12 L28 19 L42 33 L35 40 L21 26 L13 38 Z" fill="#000"/></svg>

</body>
</html>
```